Pool Screen Enclosure Building a Career Boot Camp!

Looking to Host a Boot Camp for people looking for a career or looking to change careers. We Design, Manufacture and Install Custom Pool Screen Enclosures. We have a training program to allow Non Experienced motivated people the chance at a great career that will provide a great living for them and their family. This will be a paid boot camp, week long, we provide all the initial training for them to make a transition into our business. This will be 5 days of training with a guaranteed job to start the following Monday.... This is good for both someone with no construction experience or someone with construction experience that wants to upgrade their current job.
Paid Boot Camp
transition to a full time job with great pay
Benefits include Health Insurance, Dental and Vision, 401K, we provide the tools and training.

```html
<!DOCTYPE html>
<html lang="en">
<head>
<meta charset="utf-8">
<title>Pool Screen Enclosure Building – A Career Boot Camp</title>
<link rel="stylesheet" href="https://fonts.googleapis.com/css2?family=Open+Sans:wght@400;600;700;800&display=swap">
<style>
  :root {
    --ink: #2f2f2f;
    --body-ink: #3a3a3a;
    --header-black: #000000;
    --brand-green: #52d620;
    --brand-green-light: #74e33f;
    --sun-yellow: #fbd13a;
    --paper: #ffffff;
    --divider: #3a3a3a;
  }
  * { box-sizing: border-box; margin: 0; padding: 0; }
  html, body { width: 943px; height: 1200px; overflow: hidden; background: var(--paper); }
  body { font-family: "Open Sans", Arial, sans-serif; color: var(--ink); position: relative; }

  .flyer { position: absolute; left: 0; top: 0; width: 943px; height: 1200px; background: var(--paper); overflow: hidden; }

  /* Header */
  .header { position: absolute; left: 0; top: 0; width: 943px; height: 169px; background: var(--header-black); }
  .header__brand { position: absolute; left: 46px; top: 56px; height: 36px; display: flex; align-items: center; gap: 12px;
    color: var(--brand-green); font-weight: 700; font-size: 33px; line-height: 36px; letter-spacing: -0.3px; white-space: nowrap; }
  .header__brand-dot { width: 32px; height: 32px; border-radius: 50%; background: var(--brand-green); flex: none; }
  .header__title { position: absolute; left: 547px; top: 31px; color: #fff; font-weight: 800;
    font-size: 28.5px; line-height: 35px; letter-spacing: 0.2px; text-transform: uppercase; white-space: nowrap; }

  .hero-photo { position: absolute; left: 0; top: 169px; width: 943px; height: 501px;
    background: linear-gradient(180deg, #c9cfd6 0%, #a9b2bc 45%, #6f8a5e 68%, #8fb3b4 78%, #3f6f72 100%); }

  /* Intro + points */
  .intro { position: absolute; left: 46px; top: 709px; width: 420px; font-size: 21.5px; line-height: 36px;
    font-weight: 600; color: var(--ink); white-space: nowrap; }

  .points { list-style: none; }
  .points__item { position: absolute; left: 46px; width: 384px; padding-left: 38px; font-size: 13.4px; line-height: 18.7px;
    text-align: justify; color: var(--body-ink); }
  .points__tick { position: absolute; left: 0; top: 1px; width: 17px; height: 17px; }

  /* Boot camp panel */
  .bootcamp { position: absolute; left: 499px; top: 718px; width: 444px; height: 166px; }
  .bootcamp__shape { position: absolute; left: 0; top: 0; }
  .bootcamp__title { position: absolute; left: 73px; top: 20px; color: #fff; font-weight: 800; font-size: 30px;
    line-height: 36px; letter-spacing: 0.2px; white-space: nowrap; }
  .bootcamp__list { position: absolute; left: 78px; top: 64px; list-style: none; color: #fff; font-size: 13.4px; line-height: 19px; white-space: nowrap; }
  .bootcamp__list li { position: relative; padding-left: 15px; margin-bottom: 6px; }
  .bootcamp__list li::before { content: ""; position: absolute; left: 0; top: 6px; width: 7px; height: 7px; border-radius: 50%; background: #fff; }

  /* Work photos */
  .work-photo { position: absolute; top: 901px; height: 176px; width: 211px; }
  .work-photo--roof { left: 494px; background: linear-gradient(180deg, #4f86c6 0%, #9cc0e0 45%, #dfe6ea 75%, #6b6f73 100%); }
  .work-photo--plans { left: 713px; background: linear-gradient(160deg, #b8aea0 0%, #8e8478 40%, #d8cfc4 70%, #9c9085 100%); }

  /* Footer */
  .footer__name { position: absolute; left: 46px; top: 1113px; color: var(--brand-green); font-weight: 700; font-size: 21px; line-height: 26px; white-space: nowrap; }
  .footer__address { position: absolute; left: 46px; top: 1144px; height: 18px; display: flex; align-items: center; gap: 8px;
    font-size: 12.6px; line-height: 18px; color: var(--ink); white-space: nowrap; }
  .footer__divider { position: absolute; left: 343px; top: 1123px; width: 1px; height: 44px; background: var(--divider); }
  .footer__contact { position: absolute; left: 373px; height: 18px; display: flex; align-items: center; gap: 9px;
    font-size: 12.6px; line-height: 18px; color: var(--ink); white-space: nowrap; }
  .footer__contact b { font-weight: 700; }
  .footer__contact--mail { top: 1122px; }
  .footer__contact--web { top: 1149px; }
  .icon-badge { width: 18px; height: 18px; flex: none; }

  .phone-tab { position: absolute; left: 600px; top: 1106px; width: 343px; height: 81px; }
  .phone-tab__shape { position: absolute; left: 0; top: 0; }
  .phone-tab__number { position: absolute; left: 64px; top: 29px; height: 40px; display: flex; align-items: center; gap: 10px;
    font-weight: 800; font-size: 33px; line-height: 40px; color: #111; letter-spacing: -0.3px; white-space: nowrap; }
  .bottom-strip { position: absolute; left: 0; top: 1187px; width: 943px; height: 13px; background: var(--sun-yellow); }
</style>
</head>
<body>
<main class="flyer">
  <header class="header">
    <div class="header__brand"><span class="header__brand-dot"></span>The Patio Works</div>
    <h1 class="header__title">Pool Screen<br>Enclosure Building<br>A Career Boot Camp</h1>
  </header>

  <div class="hero-photo" role="img" aria-label="Screened pool enclosure at dusk overlooking a lake and neighbouring homes"></div>

  <h2 class="intro">We Design, Manufacture and Install<br>Custom Pool Screen Enclosures.</h2>

  <ul class="points">
    <li class="points__item" style="top:799px">
      <svg class="points__tick" viewBox="0 0 20 20"><circle cx="10" cy="10" r="8.5" fill="none" stroke="#52d620" stroke-width="1.5"/><path d="M6 10.2l2.8 2.8L14 7.6" fill="none" stroke="#52d620" stroke-width="1.6"/></svg>
      We have a training program to allow Non Experienced motivated people the chance at a great career that will provide a great living for them and their family.
    </li>
    <li class="points__item" style="top:878px">
      <svg class="points__tick" viewBox="0 0 20 20"><circle cx="10" cy="10" r="8.5" fill="none" stroke="#52d620" stroke-width="1.5"/><path d="M6 10.2l2.8 2.8L14 7.6" fill="none" stroke="#52d620" stroke-width="1.6"/></svg>
      This will be a paid boot camp, week long, we provide all the initial training for them to make a transition into our business.
    </li>
    <li class="points__item" style="top:957px">
      <svg class="points__tick" viewBox="0 0 20 20"><circle cx="10" cy="10" r="8.5" fill="none" stroke="#52d620" stroke-width="1.5"/><path d="M6 10.2l2.8 2.8L14 7.6" fill="none" stroke="#52d620" stroke-width="1.6"/></svg>
      This will be 5 days of training with a guaranteed job to start the following Monday....
    </li>
    <li class="points__item" style="top:1016px">
      <svg class="points__tick" viewBox="0 0 20 20"><circle cx="10" cy="10" r="8.5" fill="none" stroke="#52d620" stroke-width="1.5"/><path d="M6 10.2l2.8 2.8L14 7.6" fill="none" stroke="#52d620" stroke-width="1.6"/></svg>
      This is good for both someone with no construction experience or someone with construction experience that wants to upgrade their current job.
    </li>
  </ul>

  <section class="bootcamp">
    <svg class="bootcamp__shape" width="444" height="166" viewBox="0 0 444 166">
      <path d="M70 0 H444 V166 H20 Q0 166 5 146 L45 18 Q51 0 70 0 Z" fill="#52d620"/>
      <path d="M70 0 H110 Q85 4 78 22 L40 140 Q34 160 20 166 Q0 166 5 146 L45 18 Q51 0 70 0 Z" fill="#74e33f" opacity="0.55"/>
    </svg>
    <h3 class="bootcamp__title">BOOT CAMP IS HERE</h3>
    <ul class="bootcamp__list">
      <li>Transition to a full time job with great pay.</li>
      <li>Benefits include Health Insurance,<br>Dental and Vision, 401K.</li>
      <li>We provide the tools and training.</li>
    </ul>
  </section>

  <div class="work-photo work-photo--roof" role="img" aria-label="Crew members fitting the frame of a white screen enclosure"></div>
  <div class="work-photo work-photo--plans" role="img" aria-label="Trainees reviewing construction plans on site"></div>

  <div class="footer__name">The Patio Works</div>
  <div class="footer__address">
    <svg class="icon-badge" viewBox="0 0 20 20"><circle cx="10" cy="10" r="9.5" fill="#111"/><path d="M10 4.5a3.6 3.6 0 0 0-3.6 3.6c0 2.7 3.6 7 3.6 7s3.6-4.3 3.6-7A3.6 3.6 0 0 0 10 4.5z" fill="#fff"/><circle cx="10" cy="8.1" r="1.4" fill="#111"/></svg>
    412 S Harbor Road, Port Lucie FL 34950
  </div>
  <div class="footer__divider"></div>
  <div class="footer__contact footer__contact--mail">
    <svg class="icon-badge" viewBox="0 0 20 20"><circle cx="10" cy="10" r="9.5" fill="#111"/><rect x="5.2" y="6.8" width="9.6" height="6.6" fill="none" stroke="#fff" stroke-width="1.1"/><path d="M5.4 7.1L10 10.6l4.6-3.5" fill="none" stroke="#fff" stroke-width="1.1"/></svg>
    <span>Admin@<b>thepatioworks</b>.com</span>
  </div>
  <div class="footer__contact footer__contact--web">
    <svg class="icon-badge" viewBox="0 0 20 20"><circle cx="10" cy="10" r="9.5" fill="#111"/><g fill="none" stroke="#fff" stroke-width="1"><circle cx="10" cy="10" r="5"/><ellipse cx="10" cy="10" rx="2.2" ry="5"/><path d="M5 10h10M5.8 7.4h8.4M5.8 12.6h8.4"/></g></svg>
    <span>www.<b>thepatioworks</b>.com</span>
  </div>

  <div class="phone-tab">
    <svg class="phone-tab__shape" width="343" height="81" viewBox="0 0 343 81">
      <path d="M64 0 H343 V81 H0 Q22 80 32 62 L50 12 Q55 0 64 0 Z" fill="#fbd13a"/>
    </svg>
    <div class="phone-tab__number">
      <svg width="22" height="22" viewBox="0 0 24 24"><path d="M6.6 2.5l3 3.6-1.9 2.3c1.2 2.6 3.3 4.7 5.9 5.9l2.3-1.9 3.6 3-1.6 3.4c-.4.8-1.3 1.2-2.2 1C9.1 18.6 5.4 14.9 4.2 8.3c-.2-.9.2-1.8 1-2.2z" fill="#111"/><path d="M14 3.5a7 7 0 0 1 6.5 6.5M14 7a3.5 3.5 0 0 1 3 3" fill="none" stroke="#111" stroke-width="1.8"/></svg>
      772-555-0147
    </div>
  </div>
  <div class="bottom-strip"></div>
</main>
</body>
</html>
```